Young Architect Bussiness Card

English is not my first language (spanish is).
Need a bussiness card design for my best friend who is about to graduate from college, Licentiate degree in architecture, so she needs business cards to start networking, currently she has no porfolio, web page or plazared. so she is relying on her cel phone and correovela, but should leave space for one of them (plazared)

Design for business card should be modern, maybe something with construction blue prints patern or 3D modelling.

Name: Mariela Otárola Bonilla
Licentiate in Arquitecture
Cel: (506) XXX-4827
email: marielaXXX@correovela.com

Services, although im not sure if it has to be there or not:
Anteproyectos / Proposal design
Inspecciones / Site Inspections
Modelado 3D / 3D modelling
Planos Constructivos / Construction Blue Prints
Presupuestos / Budgets

Design should be in spanish

Industry/Entity Type

Architect

Contact Information for Business Card

Name: Mariela Otárola, Arquitecto
Associtation code : XXXX
Phone: (506) XXXX-XXXX
Email: xxx@correovela.com
Plazared: xxxx

Requirements
Must have
• Design for business card should be modern, maybe something with construction blue prints patern or 3D modelling.
Nice to have
• Something like a transition from 2D to 3D.

```html
<!DOCTYPE html>
<html lang="es">
<head>
<meta charset="utf-8">
<title>Tarjeta de presentación – Mariela Otárola Bonilla</title>
<link href="https://fonts.googleapis.com/css2?family=Arimo:wght@400;700&display=swap" rel="stylesheet">
<style>
  :root {
    --stage: #8c8c8c;
    --navy: #143f73;
    --paper-light: #f7f7f7;
    --white: #ffffff;
    --accent-red: #d4153c;
    --ink-blue: #1c4378;
  }
  * { margin: 0; padding: 0; box-sizing: border-box; }
  html, body { width: 1073px; height: 1200px; overflow: hidden; }
  body {
    background: var(--stage);
    font-family: "Arimo", Arial, sans-serif;
    position: relative;
  }
  .card {
    position: absolute;
    left: 153px;
    width: 791px;
    overflow: hidden;
    background: var(--paper-light);
  }
  .card--front { top: 136px; height: 455px; }
  .card--back { top: 628px; height: 458px; }
  .card__art { position: absolute; inset: 0; width: 100%; height: 100%; display: block; }

  .services {
    position: absolute;
    font-weight: 700;
    font-size: 26px;
    line-height: 36px;
    white-space: nowrap;
    list-style: none;
  }
  .services--es {
    left: 124px; top: 210px;
    width: 320px;
    color: var(--white);
    text-align: center;
    transform-origin: 50% 50%;
    transform: rotate(-28deg);
    text-shadow: 2px 2px 3px rgba(0,0,0,.7);
  }
  .services--en {
    left: 380px; top: 128px;
    color: var(--ink-blue);
    text-align: left;
    transform-origin: 0 0;
    transform: rotate(-27deg);
  }

  .identity {
    position: absolute;
    left: 362px; top: 62px;
    width: 410px;
    text-align: center;
  }
  .identity__name {
    color: var(--white);
    font-weight: 700;
    font-size: 34px;
    line-height: 48px;
    text-shadow: 2px 2px 3px rgba(0,0,0,.55);
  }
  .identity__title {
    margin-top: 30px;
    color: var(--accent-red);
    font-weight: 700;
    font-size: 20px;
  }

  .contacts {
    position: absolute;
    right: 28px; top: 292px;
    list-style: none;
  }
  .contacts__item {
    display: flex;
    align-items: center;
    justify-content: flex-end;
    height: 40px;
    margin-bottom: 13px;
    color: var(--white);
    font-size: 21px;
  }
  .contacts__icon {
    width: 34px; height: 34px;
    margin-left: 24px;
    display: block;
    flex: none;
  }
</style>
</head>
<body>

<section class="card card--front" aria-label="Tarjeta, lado de servicios">
  <svg class="card__art" viewBox="0 0 791 455">
    <defs>
      <linearGradient id="paperFront" x1="0" y1="0" x2="1" y2="1">
        <stop offset="0" stop-color="#fbfbfb"/>
        <stop offset="0.6" stop-color="#e4e5e7"/>
        <stop offset="1" stop-color="#cfd0d3"/>
      </linearGradient>
    </defs>
    <rect x="0" y="0" width="791" height="455" fill="url(#paperFront)" role="img" aria-label="Rollos de planos constructivos en tonos grises"/>
    <polygon points="0,0 276,0 517,455 0,455" fill="var(--navy)"/>
  </svg>
  <ul class="services services--es">
    <li>Anteproyectos</li>
    <li>Inspecciones</li>
    <li>Modelado 3D</li>
    <li>Planos Constructivos</li>
    <li>Presupuestos</li>
  </ul>
  <ul class="services services--en">
    <li>Proposal design</li>
    <li>Site Inspections</li>
    <li>3D modelling</li>
    <li>Construction Blue Prints</li>
    <li>Budgets</li>
  </ul>
</section>

<section class="card card--back" aria-label="Tarjeta, lado de contacto">
  <svg class="card__art" viewBox="0 0 791 458">
    <defs>
      <linearGradient id="paperBack" x1="0" y1="0" x2="1" y2="1">
        <stop offset="0" stop-color="#f4f4f4"/>
        <stop offset="0.7" stop-color="#dfe0e2"/>
        <stop offset="1" stop-color="#c9cacd"/>
      </linearGradient>
    </defs>
    <rect x="0" y="0" width="791" height="458" fill="url(#paperBack)" role="img" aria-label="Plano técnico de detalles estructurales en tonos grises"/>
    <polygon points="291,0 791,0 791,458 435,458" fill="var(--navy)"/>
  </svg>

  <div class="identity">
    <h1 class="identity__name">Mariela Otárola<br>Bonilla</h1>
    <p class="identity__title">Licentiate in Arquitecture</p>
  </div>

  <ul class="contacts">
    <li class="contacts__item">
      marielaXXX@correovela.com
      <svg class="contacts__icon" viewBox="0 0 34 34" aria-hidden="true">
        <rect x="2" y="7" width="30" height="20" rx="1.5" fill="none" stroke="#fff" stroke-width="2.5"/>
        <polyline points="3,8 17,19 31,8" fill="none" stroke="#fff" stroke-width="2.5"/>
      </svg>
    </li>
    <li class="contacts__item">
      (506) XXX-4827
      <svg class="contacts__icon" viewBox="0 0 34 34" aria-hidden="true">
        <rect x="1" y="1" width="32" height="32" rx="5" fill="#fff"/>
        <path d="M11 8 L14 8 L16 13 L13.5 15 Q15 19 19 20.5 L21 18 L26 20 L26 23 Q25 26 21 26 Q9 24 8 12 Q8 8 11 8 Z" fill="var(--navy)"/>
      </svg>
    </li>
    <li class="contacts__item">
      marielaXXX
      <svg class="contacts__icon" viewBox="0 0 34 34" aria-hidden="true">
        <rect x="1" y="1" width="32" height="32" rx="3" fill="#fff"/>
      </svg>
    </li>
  </ul>
</section>

</body>
</html>
```